Heron Property Inspection business card

I am the principal inspector of Heron Property Inspections. I serve Northern Virginia from Winchester to Arlington.Associate, Federated Guild of Dwelling Examiners (FGDE)Graduate, FGDE Home Inspectors CourseNational Association of Home Inspectors ExamI'd like the business card to look more professional than comical.I pulled the attached picture off the web. I'd like to have something like that or an image of a house as my logo on the cards.

Target Market(s)

Persons who recently purchased a home.

Industry/Entity Type

Business

Contact Information for Business Card

Heron Property Inspections, LLC.4455 River RoadBluemont, Virginia 20135cell: 703-231-6680e-mail: tkmarlow@postvale.net

Font styles to use
Serif
Sans Serif

Requirements
Must have
• I'd like to have a logo, something that identifies me as a home inspector. The attached images are something that I'd like to have incorporated into my business card logo.
Nice to have
• I'd like a sketch of a house and/or a magnifying glass showing a house being inspected. The attached images are used as a suggestion only, I do not own the images.
Should not have
• Gimmicky stuff. I want to appear professional and trustworthy.

```html
<!DOCTYPE html>
<html lang="en">
<head>
<meta charset="utf-8">
<title>Heron Property Inspections – Business Card</title>
<link href="https://fonts.googleapis.com/css2?family=Cinzel:wght@600&family=Open+Sans:wght@400;600&display=swap" rel="stylesheet">
<style>
  :root {
    --page-bg: #e9e7e4;
    --card-white: #ffffff;
    --card-grey-light: #8a8a8a;
    --card-grey-dark: #5a5a5a;
    --accent-blue: #3cc3e6;
    --accent-blue-deep: #1d9fd0;
    --brand-navy: #24388f;
    --text-light: #ffffff;
    --text-soft: #e4e4e4;
  }
  * { margin: 0; padding: 0; box-sizing: border-box; }
  html, body {
    width: 1200px; height: 818px; overflow: hidden;
    background: var(--page-bg);
  }
  .canvas {
    position: relative; width: 1200px; height: 818px;
    display: flex; align-items: center; justify-content: center;
  }
  .card {
    position: relative; width: 980px; height: 560px;
    background: var(--card-white);
    box-shadow: 0 14px 40px rgba(0,0,0,0.22);
    overflow: hidden;
  }
  .card-shapes { position: absolute; inset: 0; }
  .brand {
    position: absolute; left: 40px; top: 200px; width: 360px;
    display: flex; flex-direction: column; align-items: center; gap: 18px;
  }
  .brand-mark {
    width: 70px; height: 70px; border-radius: 50%;
    border: 6px solid var(--accent-blue-deep);
  }
  .brand-name {
    font-family: "Cinzel", serif; font-weight: 600;
    color: var(--brand-navy); font-size: 27px; line-height: 1.25;
    text-align: center; letter-spacing: 0.5px;
  }
  .person {
    position: absolute; left: 560px; top: 96px;
    font-family: "Open Sans", sans-serif; color: var(--text-light);
  }
  .person-name { font-size: 44px; font-weight: 600; letter-spacing: 0.5px; }
  .person-title { font-size: 21px; color: var(--text-soft); margin-top: 2px; }
  .contact {
    position: absolute; left: 600px; top: 290px;
    font-family: "Open Sans", sans-serif; color: var(--text-light);
    font-size: 22px; line-height: 1.45;
  }
  .contact-row { display: flex; align-items: center; gap: 12px; }
  .contact-row.indent { padding-left: 40px; }
  .contact-icon {
    width: 28px; height: 24px; background: var(--text-light);
    border-radius: 3px; display: flex; align-items: center; justify-content: center;
  }
</style>
</head>
<body>
<main class="canvas">
  <section class="card" aria-label="Heron Property Inspections business card">
    <svg class="card-shapes" width="980" height="560" viewBox="0 0 980 560" aria-hidden="true">
      <defs>
        <linearGradient id="panelGrey" x1="0" y1="0" x2="1" y2="1">
          <stop offset="0" stop-color="var(--card-grey-light)"/>
          <stop offset="1" stop-color="var(--card-grey-dark)"/>
        </linearGradient>
        <linearGradient id="bandBlue" x1="0" y1="0" x2="0" y2="1">
          <stop offset="0" stop-color="var(--accent-blue-deep)"/>
          <stop offset="1" stop-color="var(--accent-blue)"/>
        </linearGradient>
      </defs>
      <path class="info-panel" d="M390 0 Q480 250 535 560 L980 560 L980 0 Z" fill="url(#panelGrey)"/>
      <path class="accent-band" d="M355 0 Q455 250 517 560 L535 560 Q480 250 390 0 Z" fill="url(#bandBlue)"/>
    </svg>

    <div class="brand">
      <div class="brand-mark"></div>
      <div class="brand-name">Heron Property<br>Inspections, LLC</div>
    </div>

    <div class="person">
      <div class="person-name">Employee Name</div>
      <div class="person-title">Managing Director</div>
    </div>

    <div class="contact">
      <div class="contact-row">
        <span class="contact-icon">
          <svg width="12" height="18" viewBox="0 0 12 18" aria-hidden="true"><rect x="1" y="1" width="10" height="16" rx="2" fill="none" stroke="#5a5a5a" stroke-width="2"/><circle cx="6" cy="14" r="1.2" fill="#5a5a5a"/></svg>
        </span>
        <span>703-555-0192</span>
      </div>
      <div class="contact-row">
        <span class="contact-icon">
          <svg width="20" height="14" viewBox="0 0 20 14" aria-hidden="true"><rect x="1" y="1" width="18" height="12" fill="none" stroke="#1d4f9f" stroke-width="2"/><path d="M1 1 L10 8 L19 1" fill="none" stroke="#1d4f9f" stroke-width="2"/></svg>
        </span>
        <span>tkmarlow@postvale.net</span>
      </div>
      <div class="contact-row indent"><span>7182 Quarry Lane Fernhill</span></div>
      <div class="contact-row indent"><span>Virginia 20148</span></div>
    </div>
  </section>
</main>
</body>
</html>
```